The most modern business card ever !!!

Our company call “Vendalo”. Vendalo is a technology company specialized in cruises solutions. Out main product is a platform to reserve cruises. This is a revolutionary platform that make easier to travel agencies and final users to reserve cruises across dozen companies like tibba, wernu, hpv, dgb, etc..We are a “start up”, with a young team of developers and we want to transmit it.. For it, we want something different, a modern business card that represent cruises and technology.. When someone receive this card, this person should say: wowww this is different… this is modern… this is a cruise related company..
- diferent, modern
- traditions business card

```html
<!DOCTYPE html>
<html lang="en">
<head>
<meta charset="utf-8">
<title>Vendalo Business Card</title>
<link href="https://fonts.googleapis.com/css2?family=Exo+2:wght@400;500;700&family=Roboto:wght@400&display=swap" rel="stylesheet">
<style>
  :root {
    --backdrop: #6a6a6a;
    --ink: #111111;
    --brand-blue: #29a9e0;
    --panel-black: #000000;
    --paper: #ffffff;
    --strip-grey: #e6e6e6;
    --text-light: #ffffff;
  }
  html, body {
    margin: 0;
    padding: 0;
    width: 1200px;
    height: 802px;
    overflow: hidden;
    background: var(--backdrop);
  }
  .stage {
    position: relative;
    width: 1200px;
    height: 802px;
  }
  .card {
    position: absolute;
    top: 274px;
    width: 442px;
    height: 265px;
    overflow: hidden;
    box-shadow: 0 4px 10px rgba(0,0,0,0.35);
  }
  .card--front {
    left: 136px;
    background: var(--brand-blue);
  }
  .card--back {
    left: 624px;
    background: var(--paper);
  }
  .front__panel {
    position: absolute;
    left: 0;
    top: 0;
    width: 120px;
    height: 100%;
    background: var(--panel-black);
  }
  .front__details {
    position: absolute;
    right: 22px;
    top: 60px;
    text-align: right;
    color: var(--text-light);
    font-family: "Exo 2", sans-serif;
  }
  .person__name {
    margin: 0;
    font-weight: 700;
    font-size: 17px;
    line-height: 18px;
    letter-spacing: 0.2px;
  }
  .person__role {
    margin: 0 0 12px;
    font-family: "Roboto", sans-serif;
    font-size: 12.5px;
    line-height: 14px;
  }
  .contact-list {
    list-style: none;
    margin: 0 0 9px;
    padding: 0;
    font-size: 12.5px;
    line-height: 16px;
  }
  .contact-list li {
    display: flex;
    justify-content: flex-end;
    align-items: center;
    gap: 3px;
  }
  .contact-icon {
    width: 10px;
    height: 10px;
    fill: var(--text-light);
  }
  .address {
    margin: 0;
    font-style: normal;
    font-size: 12.5px;
    line-height: 16px;
  }
  .back__strip {
    position: absolute;
    left: 0;
    top: 0;
    width: 45px;
    height: 100%;
    background: var(--strip-grey);
  }
  .brand-name {
    position: absolute;
    left: 45px;
    right: 0;
    top: 0;
    height: 100%;
    display: flex;
    align-items: center;
    justify-content: center;
    margin: 0;
    font-family: "Exo 2", sans-serif;
    font-weight: 500;
    font-size: 52px;
    letter-spacing: 2px;
    color: var(--ink);
  }
</style>
</head>
<body>
<main class="stage">
  <section class="card card--front" aria-label="Card front">
    <div class="front__panel"></div>
    <div class="front__details">
      <h1 class="person__name">MARCUS ELLERY</h1>
      <p class="person__role">Managing Director</p>
      <ul class="contact-list">
        <li>044-310 582 417
          <svg class="contact-icon" viewBox="0 0 10 10" aria-hidden="true"><path d="M1 3.5c0-1.5 8-1.5 8 0v1H7V3.6H3v.9H1z"/><rect x="2" y="5" width="6" height="4" rx="1"/></svg>
        </li>
        <li>044-310 582 417
          <svg class="contact-icon" viewBox="0 0 10 10" aria-hidden="true"><path d="M2.5 0h5a.8.8 0 0 1 .8.8v8.4a.8.8 0 0 1-.8.8h-5a.8.8 0 0 1-.8-.8V.8a.8.8 0 0 1 .8-.8zm.4 1.2v6.6h4.2V1.2z"/></svg>
        </li>
        <li>info@vendalo.com
          <svg class="contact-icon" viewBox="0 0 10 10" aria-hidden="true"><path d="M0 2h10v6H0z M0.8 2.6 5 5.6 9.2 2.6" stroke="#29a9e0" stroke-width="0.8"/></svg>
        </li>
        <li>www.vendalo.com
          <svg class="contact-icon" viewBox="0 0 10 10" aria-hidden="true"><circle cx="5" cy="5" r="4.8"/><path d="M3 3.2c1 .2 1.5 1 1.2 1.8L5.5 6.5 4.5 8.6M6.5 1.5c-.3 1 .4 1.6 1.5 1.6" stroke="#29a9e0" stroke-width="0.8" fill="none"/></svg>
        </li>
      </ul>
      <address class="address">4821, Harbour Lane<br>Portmere, 204517</address>
    </div>
  </section>

  <section class="card card--back" aria-label="Card back">
    <div class="back__strip"></div>
    <p class="brand-name">Vendalo</p>
  </section>
</main>
</body>
</html>
```